Need Web Design for Business Process Outsourcing Company (Quorvane)

Quorvane is a business process outsourcing company. Need a simple site similar to http://www.tallowbrinkhire.com/ but with a more professional and credible look. New to the process; not sure where to start and comparing my options. Please let me know what my options are if I choose to go with you. Logo is attached for your reference. Please use same colorway

Reason: I want the final product to be coded. Please confirm you will be able to code final design.

Industry/Entity Type

Business

Coding

Coded - Design and coding required

```html
<!DOCTYPE html>
<html lang="en">
<head>
<meta charset="utf-8">
<title>Quorvane Services</title>
<link rel="stylesheet" href="https://fonts.googleapis.com/css2?family=Open+Sans:wght@400;600;700&family=Roboto+Condensed:wght@300;400;700&display=swap">
<style>
:root{
  --blue:#1a8fd1;
  --blue-bright:#0c8ed3;
  --navy:#0e4f7e;
  --ink:#333;
  --text:#555;
  --nav:#3a3a3a;
  --footer:#3d3d3d;
  --copyright:#10406a;
  --white:#fff;
}
*{margin:0;padding:0;box-sizing:border-box}
html,body{width:1200px;height:3727px;overflow:hidden}
body{font-family:"Open Sans",Arial,sans-serif;color:var(--text);background:var(--white)}
.container{width:1046px;margin:0 auto;position:relative}
.heading{font-family:"Roboto Condensed","Arial Narrow",sans-serif;font-weight:400;font-size:44px;color:var(--ink);text-align:center;letter-spacing:.5px}
.heading span{color:var(--blue)}
.lead{font-size:15px;line-height:27px;text-align:center}
.btn{display:inline-flex;align-items:center;gap:8px;background:var(--navy);color:var(--white);font-size:17px;text-transform:uppercase;padding:0 22px;height:52px;text-decoration:none}
.btn svg{width:14px;height:14px}

/* hero */
.hero{height:678px;position:relative;background:linear-gradient(180deg,#0d3f62 0%,#2f7bab 38%,#8cc0dd 62%,#1d5f8c 100%)}
.hero-brand{position:absolute;left:0;right:0;top:78px;display:flex;flex-direction:column;align-items:center;gap:34px}
.hero-brand .mark{width:96px;height:96px;background:#1466a4}
.hero-brand .name{font-family:"Roboto Condensed","Arial Narrow",sans-serif;font-weight:700;font-size:96px;color:#2b323b;line-height:1}

/* nav */
.main-nav{height:57px;background:var(--nav)}
.main-nav ul{list-style:none;display:flex;height:57px}
.main-nav a{display:flex;align-items:center;height:57px;padding:0 23px;color:var(--white);text-decoration:none;font-size:16px;text-transform:uppercase}
.main-nav a.active{background:var(--blue-bright)}

/* welcome */
.welcome{height:378px;padding-top:52px;text-align:center}
.welcome .lead{width:935px;margin:24px auto 26px}

/* services */
.services{height:725px;position:relative;background:radial-gradient(circle at 55% 55%,#1a9de0 0%,#0b84c8 45%,#0668a8 100%);color:var(--white)}
.services .heading{color:var(--white);padding-top:50px}
.services .intro{font-size:15px;text-align:center;margin-top:14px}
.service{position:absolute;width:300px}
.service h3{font-family:"Roboto Condensed","Arial Narrow",sans-serif;font-weight:400;font-size:25px;margin-bottom:12px}
.service p{font-size:14px;line-height:24px}
.service.right{text-align:right}
.service-map{position:absolute;left:0;top:0;width:1200px;height:725px}

/* strategy */
.strategy{height:497px;padding-top:52px;text-align:center}
.strategy .lead{width:820px;margin:22px auto 46px}
.pillars{display:flex;gap:0;text-align:left}
.pillar{width:360px;display:flex;gap:24px}
.pillar .icon{width:127px;height:127px;background:var(--navy);flex:none;display:flex;align-items:center;justify-content:center}
.pillar .icon svg{width:76px;height:76px}
.pillar h3{font-family:"Roboto Condensed","Arial Narrow",sans-serif;font-weight:400;font-size:25px;color:var(--blue);margin:0 0 10px}
.pillar p{font-size:15px;line-height:25px;width:170px}
.strategy .btn{margin-top:52px}

/* experience */
.experience{height:504px;padding-top:52px;background:linear-gradient(180deg,#4d4d4d,#5b5b5b 60%,#4a4a4a);color:var(--white);text-align:center}
.experience .heading{color:var(--white)}
.experience .lead{width:820px;margin:18px auto 40px}
.cards{display:flex;gap:35px;text-align:left}
.card{width:236px}
.card .photo{height:134px}
.card h3{font-family:"Roboto Condensed","Arial Narrow",sans-serif;font-weight:400;font-size:24px;margin:22px 0 8px}
.card p{font-size:15px;line-height:25px}
.card p a{color:var(--white);text-decoration:none;text-transform:uppercase;margin-left:6px}

/* security */
.security{height:124px;background:var(--blue-bright);color:var(--white)}
.security .container{height:124px;display:flex;align-items:center}
.security .lock{width:106px;height:120px;margin-left:65px;background:linear-gradient(180deg,#c9d3db,#7e8c98)}
.security .copy{margin-left:42px}
.security h2{font-family:"Roboto Condensed","Arial Narrow",sans-serif;font-weight:400;font-size:44px;line-height:1}
.security p{font-size:15px;margin-top:4px}
.security .contact-btn{margin-left:auto;margin-right:67px;background:var(--white);color:var(--ink);font-size:16px;text-transform:uppercase;height:43px;padding:0 20px;display:flex;align-items:center;text-decoration:none}

/* news */
.news{height:502px;padding-top:52px}
.news .cards{margin-top:40px}
.news .photo{height:140px}
.news h3{font-family:"Open Sans",Arial,sans-serif;font-weight:400;font-size:15px;line-height:25px;color:var(--blue);margin:14px 0 4px}
.news .date{font-size:14px;color:#999;display:flex;align-items:center;gap:8px}
.news .date svg{width:13px;height:13px}
.news .card p{color:var(--text);margin-top:8px}

/* footer */
.site-footer{height:211px;background:var(--footer);color:var(--white)}
.footer-top{display:flex;align-items:center;height:64px;border-bottom:1px solid #555}
.footer-top ul{list-style:none;display:flex;gap:22px}
.footer-top a{color:var(--white);text-decoration:none;font-size:15px}
.social{margin-left:auto;display:flex;gap:30px}
.social span{width:18px;height:18px;border-radius:50%;background:var(--white);opacity:.9}
.social span:first-child{background:var(--blue-bright)}
.site-footer h4{font-family:"Roboto Condensed","Arial Narrow",sans-serif;font-weight:400;font-size:24px;margin:18px 0 16px}
.contacts{display:flex}
.contact{width:271px;display:flex;align-items:center;gap:18px;font-size:15px;line-height:24px}
.contact .dot{width:40px;height:40px;border-radius:50%;background:var(--white);flex:none;display:flex;align-items:center;justify-content:center}
.contact .dot.blue{background:var(--blue-bright)}
.contact .dot svg{width:20px;height:20px}
.copyright{height:51px;background:var(--copyright);color:var(--white);font-size:14px;display:flex;align-items:center;justify-content:center}
.copyright b{font-weight:700;margin-right:6px}
</style>
</head>
<body>

<header class="hero" role="img" aria-label="Photo looking up between glass office towers against the sky">
  <div class="hero-brand">
    <div class="mark"></div>
    <div class="name">Quorvane</div>
  </div>
</header>

<nav class="main-nav">
  <div class="container">
    <ul>
      <li><a class="active" href="#">Home</a></li>
      <li><a href="#">Who We Are</a></li>
      <li><a href="#">Services</a></li>
      <li><a href="#">Strategy</a></li>
      <li><a href="#">Experience</a></li>
      <li><a href="#">Security</a></li>
      <li><a href="#">News</a></li>
      <li><a href="#">Contact Us</a></li>
    </ul>
  </div>
</nav>

<section class="welcome">
  <h1 class="heading">WELCOME TO <span>QUORVANE SERVICES</span></h1>
  <p class="lead">Lorem Ipsum is simply dummy text of the printing and typesetting industry. Lorem Ipsum has been the industry's standard dummy text ever since the 1500s, when an unknown printer took a galley of type and scrambled it to make a type specimen book. It has survived not only five centuries, but also the leap into electronic typesetting, remaining essentially unchanged. It was popularised in the 1960s with the release of Letraset sheets containing Lorem Ipsum is simply dummy text of the printing and typesetting industry. Lorem Ipsum has been the industry's standard.</p>
  <a class="btn" href="#">Read More <svg viewBox="0 0 14 14" fill="none" stroke="#fff" stroke-width="2"><path d="M2 2l5 5-5 5M7 2l5 5-5 5"/></svg></a>
</section>

<section class="services">
  <svg class="service-map" viewBox="0 0 1200 725" fill="none">
    <g stroke="rgba(255,255,255,.55)" stroke-width="1.5">
      <path d="M77 202H515L560 238"/>
      <path d="M77 390H330L370 377"/>
      <path d="M77 595H410L440 593"/>
      <path d="M1123 282H905L845 350"/>
      <path d="M1123 515H860L770 593"/>
      <path d="M618 300L596 322"/>
      <path d="M467 377H516"/>
      <path d="M733 377H676"/>
      <path d="M525 570L545 482"/>
      <path d="M680 570L650 482"/>
    </g>
    <rect x="516" y="322" width="160" height="160" fill="none" stroke="#fff" stroke-width="10"/>
    <g fill="#fff">
      <circle cx="618" cy="238" r="62"/>
      <circle cx="405" cy="377" r="62"/>
      <circle cx="795" cy="377" r="62"/>
      <circle cx="484" cy="593" r="62"/>
      <circle cx="713" cy="593" r="62"/>
    </g>
    <g fill="#0b84c8" stroke="#0b84c8">
      <!-- headset -->
      <circle cx="618" cy="232" r="13" stroke="none"/>
      <path d="M598 238v-8a20 20 0 0 1 40 0v8" fill="none" stroke-width="4"/>
      <rect x="594" y="232" width="8" height="14" rx="3" stroke="none"/>
      <rect x="634" y="232" width="8" height="14" rx="3" stroke="none"/>
      <path d="M600 268a18 18 0 0 1 36 0z" stroke="none"/>
      <!-- cart -->
      <path d="M380 360h8l8 30h28l6-22h-38" fill="none" stroke-width="4"/>
      <path d="M398 370h28M400 380h25" fill="none" stroke-width="3"/>
      <circle cx="400" cy="398" r="4" stroke="none"/>
      <circle cx="422" cy="398" r="4" stroke="none"/>
      <!-- server -->
      <rect x="777" y="353" width="36" height="12" stroke="none"/>
      <rect x="777" y="369" width="36" height="12" stroke="none"/>
      <rect x="777" y="385" width="36" height="12" stroke="none"/>
      <path d="M795 397v8M783 405h24" fill="none" stroke-width="3"/>
      <!-- bulb -->
      <circle cx="484" cy="586" r="15" stroke="none"/>
      <rect x="477" y="600" width="14" height="10" stroke="none"/>
      <path d="M484 560v-6M462 566l-5-5M506 566l5-5M458 586h-7M510 586h7" fill="none" stroke-width="3"/>
      <!-- people -->
      <circle cx="713" cy="575" r="8" stroke="none"/>
      <circle cx="697" cy="583" r="6" stroke="none"/>
      <circle cx="729" cy="583" r="6" stroke="none"/>
      <path d="M699 610a14 14 0 0 1 28 0zM686 606a11 11 0 0 1 20-4v4zM720 602a11 11 0 0 1 20 4z" stroke="none"/>
    </g>
    <text x="596" y="410" fill="#fff" font-family="Roboto Condensed, Arial Narrow, sans-serif" font-size="30" text-anchor="middle">Quorvane</text>
  </svg>

  <h2 class="heading">SERVICES WE PROVIDE</h2>
  <p class="intro">Lorem Ipsum is simply dummy text of the printing and typesetting industry.</p>

  <div class="service" style="left:77px;top:170px"><h3>Customer Service</h3><p>Lorem Ipsum is simply dummy text of the printing and typesetting industry.Lorem Ipsum has been the industry's.</p></div>
  <div class="service right" style="right:77px;top:250px;width:230px"><h3>IT Solutions</h3><p>Lorem Ipsum is simply dummy text of the printing and typesetting industry.</p></div>
  <div class="service" style="left:77px;top:358px;width:270px"><h3>Ecommerce</h3><p>Lorem Ipsum is simply dummy text of the printing and typesetting industry.Lorem Ipsum has been.</p></div>
  <div class="service right" style="right:77px;top:482px;width:230px"><h3>Human Resources</h3><p>Lorem Ipsum is simply dummy text of the printing and typesetting industry.</p></div>
  <div class="service" style="left:77px;top:562px;width:280px"><h3>Creative</h3><p>Lorem Ipsum is simply dummy text of the printing and typesetting industry.Lorem Ipsum has been.</p></div>
</section>

<section class="strategy">
  <div class="container">
    <h2 class="heading">OUR <span>STRATEGY</span></h2>
    <p class="lead">Lorem Ipsum is simply dummy text of the printing and typesetting industry. Lorem Ipsum has been the industry's standard dummy text ever since the 1500s.</p>
    <div class="pillars">
      <div class="pillar">
        <div class="icon"><svg viewBox="0 0 76 76" fill="#fff"><circle cx="22" cy="20" r="8"/><circle cx="50" cy="20" r="8"/><path d="M8 48a14 14 0 0 1 28 0zM36 48a14 14 0 0 1 28 0z"/><circle cx="44" cy="50" r="12" fill="none" stroke="#fff" stroke-width="5"/><path d="M52 58l14 14" stroke="#fff" stroke-width="6"/></svg></div>
        <div><h3>Lorem Ipsum</h3><p>Lorem Ipsum is simply dummy text of the printing and typesetting...</p></div>
      </div>
      <div class="pillar">
        <div class="icon"><svg viewBox="0 0 76 76" fill="#fff"><rect x="22" y="6" width="48" height="32" fill="none" stroke="#fff" stroke-width="3"/><path d="M28 30l10-10 8 6 14-14" fill="none" stroke="#fff" stroke-width="3"/><circle cx="12" cy="18" r="6"/><path d="M4 40a8 10 0 0 1 16 0z"/><circle cx="16" cy="52" r="5"/><circle cx="32" cy="52" r="5"/><circle cx="48" cy="52" r="5"/><circle cx="64" cy="52" r="5"/><path d="M8 70a8 9 0 0 1 16 0zM24 70a8 9 0 0 1 16 0zM40 70a8 9 0 0 1 16 0zM56 70a8 9 0 0 1 16 0z"/></svg></div>
        <div><h3>Lorem Ipsum</h3><p>Lorem Ipsum is simply dummy text of the printing and typesetting...</p></div>
      </div>
      <div class="pillar">
        <div class="icon"><svg viewBox="0 0 76 76" fill="#fff"><path d="M36 6c16 0 28 11 28 26 0 8-4 13-8 17v21H30v-9h-10c-4 0-6-3-6-6v-8H8l8-14C16 17 24 6 36 6z"/><circle cx="38" cy="31" r="9" fill="#0e4f7e"/><circle cx="38" cy="31" r="4" fill="#fff"/></svg></div>
        <div><h3>Lorem Ipsum</h3><p>Lorem Ipsum is simply dummy text of the printing and typesetting...</p></div>
      </div>
    </div>
    <a class="btn" href="#">Know More <svg viewBox="0 0 14 14" fill="none" stroke="#fff" stroke-width="2"><path d="M2 2l5 5-5 5M7 2l5 5-5 5"/></svg></a>
  </div>
</section>

<section class="experience" role="img" aria-label="Dimmed photo of colleagues meeting around a table">
  <div class="container">
    <h2 class="heading">OUR EXPERIENCE</h2>
    <p class="lead">Lorem Ipsum is simply dummy text of the printing and typesetting industry. Lorem Ipsum has been the industry's standard dummy text ever since the 1500s.</p>
    <div class="cards">
      <div class="card"><div class="photo" role="img" aria-label="Business team at a laptop" style="background:linear-gradient(135deg,#c8d3dc,#6f7e8a)"></div><h3>Lorem Ipsum is simply</h3><p>Lorem Ipsum is simply dummy text of the... <a href="#">Read More &#187;</a></p></div>
      <div class="card"><div class="photo" role="img" aria-label="Magnifier over financial charts" style="background:linear-gradient(135deg,#e8eef3,#8faecb)"></div><h3>Lorem Ipsum is simply</h3><p>Lorem Ipsum is simply dummy text of the... <a href="#">Read More &#187;</a></p></div>
      <div class="card"><div class="photo" role="img" aria-label="Presenter at a whiteboard with colleagues" style="background:linear-gradient(135deg,#f1f1f1,#a9b3bb)"></div><h3>Lorem Ipsum is simply</h3><p>Lorem Ipsum is simply dummy text of the... <a href="#">Read More &#187;</a></p></div>
      <div class="card"><div class="photo" role="img" aria-label="Hands reviewing documents and a tablet" style="background:linear-gradient(135deg,#b9a690,#5e4c3c)"></div><h3>Lorem Ipsum is simply</h3><p>Lorem Ipsum is simply dummy text of the... <a href="#">Read More &#187;</a></p></div>
    </div>
  </div>
</section>

<section class="security">
  <div class="container">
    <div class="lock" role="img" aria-label="Padlock illustration"></div>
    <div class="copy">
      <h2>SECURITY</h2>
      <p>Lorem Ipsum is simply dummy text of the printing and typesetting industry.</p>
    </div>
    <a class="contact-btn" href="#">Contact Us</a>
  </div>
</section>

<section class="news">
  <div class="container">
    <h2 class="heading">LATEST <span>NEWS</span></h2>
    <div class="cards">
      <div class="card"><div class="photo" role="img" aria-label="Office workers at a laptop" style="background:linear-gradient(135deg,#dfe5ea,#6b7680)"></div><h3>Lorem Ipsum is simply dummy text of the printing.</h3><div class="date"><svg viewBox="0 0 13 13" fill="none" stroke="#999"><rect x="1" y="2" width="11" height="10"/><path d="M1 5h11M4 0v3M9 0v3"/></svg>November 14, 2016</div><p>Lorem Ipsum is simply dummy text of the printing and typesetting industry.</p></div>
      <div class="card"><div class="photo" role="img" aria-label="Planning notes on a desk" style="background:linear-gradient(135deg,#d9c9a6,#7d8a95)"></div><h3>Lorem Ipsum is simply dummy text of the printing.</h3><div class="date"><svg viewBox="0 0 13 13" fill="none" stroke="#999"><rect x="1" y="2" width="11" height="10"/><path d="M1 5h11M4 0v3M9 0v3"/></svg>November 14, 2016</div><p>Lorem Ipsum is simply dummy text of the printing and typesetting industry.</p></div>
      <div class="card"><div class="photo" role="img" aria-label="Business people in an office" style="background:linear-gradient(135deg,#c6d2dc,#3f4c58)"></div><h3>Lorem Ipsum is simply dummy text of the printing.</h3><div class="date"><svg viewBox="0 0 13 13" fill="none" stroke="#999"><rect x="1" y="2" width="11" height="10"/><path d="M1 5h11M4 0v3M9 0v3"/></svg>November 14, 2016</div><p>Lorem Ipsum is simply dummy text of the printing and typesetting industry.</p></div>
      <div class="card"><div class="photo" role="img" aria-label="Hand drawing growth charts" style="background:linear-gradient(135deg,#eef2f6,#8fb0d0)"></div><h3>Lorem Ipsum is simply dummy text of the printing.</h3><div class="date"><svg viewBox="0 0 13 13" fill="none" stroke="#999"><rect x="1" y="2" width="11" height="10"/><path d="M1 5h11M4 0v3M9 0v3"/></svg>November 14, 2016</div><p>Lorem Ipsum is simply dummy text of the printing and typesetting industry.</p></div>
    </div>
  </div>
</section>

<footer class="site-footer">
  <div class="container">
    <div class="footer-top">
      <ul>
        <li><a href="#">Home</a></li><li><a href="#">Who We Are</a></li><li><a href="#">Services</a></li><li><a href="#">Strategy</a></li><li><a href="#">Experience</a></li><li><a href="#">Security</a></li><li><a href="#">News</a></li><li><a href="#">Contact Us</a></li>
      </ul>
      <div class="social"><span></span><span></span><span></span></div>
    </div>
    <h4>Contact Us</h4>
    <div class="contacts">
      <div class="contact"><span class="dot blue"><svg viewBox="0 0 20 20" fill="#fff"><path d="M10 1a6 6 0 0 1 6 6c0 5-6 12-6 12S4 12 4 7a6 6 0 0 1 6-6z"/><circle cx="10" cy="7" r="2.3" fill="#0c8ed3"/></svg></span>Lorem Ipsum is simply<br>dummy text of the.</div>
      <div class="contact"><span class="dot"><svg viewBox="0 0 20 20" fill="none" stroke="#0c8ed3" stroke-width="2"><rect x="5" y="1" width="10" height="18" rx="2"/><path d="M9 16h2"/></svg></span>123 456 7890</div>
      <div class="contact"><span class="dot"><svg viewBox="0 0 20 20" fill="#0c8ed3"><rect x="3" y="7" width="14" height="12" rx="1"/><rect x="6" y="1" width="8" height="6"/><rect x="6" y="10" width="2" height="2" fill="#fff"/><rect x="9" y="10" width="2" height="2" fill="#fff"/><rect x="12" y="10" width="2" height="2" fill="#fff"/><rect x="6" y="14" width="2" height="2" fill="#fff"/><rect x="9" y="14" width="2" height="2" fill="#fff"/><rect x="12" y="14" width="2" height="2" fill="#fff"/></svg></span>123 456 7890</div>
      <div class="contact"><span class="dot"><svg viewBox="0 0 20 20" fill="none" stroke="#0c8ed3" stroke-width="2"><rect x="2" y="4" width="16" height="12"/><path d="M2 4l8 7 8-7"/></svg></span>Lorem Ipsum is simply</div>
    </div>
  </div>
</footer>
<div class="copyright"><b>© QUORVANE SERVICES - 2016.</b> All Rights Reserved.</div>

</body>
</html>
```